New Fun, Positive, energised looking Business Card Needed for High Achiever Coach

I am looking for a two sided full colour business card. I am self employed and have recently re branded my 1-2-1 work re-vitalising high achievers. My target client base for these cards is therefore high achievers - usually aged 40 -55, they are often entrepreneurs, CEO or work in banking and finance and 2/3 are male. I work with them on 90 day or 6 month coaching programs to help them live their success in a healthier, more sustainable and fulfiiled way. They pay for this privately so though they are corporate types the cards need not look 'corporate'. I want to portray the idea of transformation, vitality and re-connecting.
You can get a feel for the look I like on my new website: morvenlisk.co.uk
I want to use this logo with strapline (Re-Vitalising High Achievers) (I purchased off Logoharbor) and font/ colours (the turquoise and green).
Details to include on the card:
www.morvenlisk.co.uk
+44 7915 302618
morven@morvenlisk.co.uk
callnest: morvenlisk
I'd also like to include:
Do you struggle to switch off? Want to be healthier and feel fitter? Want closer relationships? More clarity over the direction you are headed? I can help you do these things using integrated mind-body techniques. Visit morvenlisk.co.uk TODAY to apply for a FREE Breakthrough session.
BUT if that is too much text for a card I am open to advice/ammendments.
Updates
Thanks for your design - I am considering them. PLease change the wording to :

```html
<!DOCTYPE html>
<html lang="en">
<head>
<meta charset="UTF-8">
<title>Morven Lisk – Business Card</title>
<link rel="stylesheet" href="https://fonts.googleapis.com/css2?family=Arvo:wght@700&family=Kaushan+Script&family=Open+Sans:wght@400;600;700&display=swap">
<style>
  :root {
    --stage: #3a3a3a;
    --paper: #ffffff;
    --paper-shade: #ececec;
    --brand-green: #58b95f;
    --brand-green-light: #66c26c;
    --brand-blue: #0ba2c8;
    --brand-blue-deep: #0790b3;
    --ink-light: #ffffff;
  }
  * { margin: 0; padding: 0; box-sizing: border-box; }
  html, body {
    width: 1200px;
    height: 900px;
    overflow: hidden;
    background: var(--stage);
  }
  .sheet {
    position: relative;
    width: 1200px;
    height: 900px;
    display: flex;
    align-items: center;
    justify-content: center;
    gap: 40px;
  }
  .card {
    position: relative;
    width: 540px;
    height: 320px;
    border-radius: 20px;
    overflow: hidden;
    box-shadow: 0 10px 30px rgba(0,0,0,0.45);
  }
  /* Front */
  .card-front { background: linear-gradient(135deg, var(--paper) 55%, var(--paper-shade)); }
  .card-front .panel-art {
    position: absolute;
    inset: 0;
    width: 100%;
    height: 100%;
  }
  .identity {
    position: absolute;
    left: 0;
    top: 0;
    width: 270px;
    height: 320px;
    text-align: center;
  }
  .identity .brand-dot {
    position: absolute;
    left: 92px;
    top: 30px;
    width: 86px;
    height: 86px;
    border-radius: 50%;
    background: var(--brand-green);
  }
  .identity .holder-name {
    position: absolute;
    left: 0;
    width: 270px;
    top: 142px;
    font-family: "Arvo", Georgia, serif;
    font-weight: 700;
    font-size: 37px;
    color: var(--brand-blue);
    letter-spacing: 0.5px;
  }
  .identity .strapline {
    position: absolute;
    left: 0;
    width: 270px;
    top: 192px;
    font-family: "Kaushan Script", cursive;
    font-size: 19px;
    color: var(--brand-blue);
  }
  .contact-list {
    position: absolute;
    left: 285px;
    top: 188px;
    list-style: none;
    font-family: "Open Sans", Arial, sans-serif;
    font-size: 16px;
    color: var(--ink-light);
  }
  .contact-list li {
    display: flex;
    align-items: center;
    height: 26px;
  }
  .contact-list .icon {
    width: 18px;
    height: 18px;
    margin-right: 14px;
    flex: none;
  }
  .contact-list .icon-label {
    font-weight: 700;
    font-size: 11px;
    width: 42px;
    margin-right: 4px;
    margin-left: -10px;
  }
  /* Back */
  .card-back {
    background: linear-gradient(160deg, var(--brand-blue) 60%, var(--brand-blue-deep));
    display: flex;
    align-items: center;
    justify-content: center;
  }
  .card-back .back-name {
    font-family: "Arvo", Georgia, serif;
    font-weight: 700;
    font-size: 44px;
    color: var(--ink-light);
    letter-spacing: 1px;
  }
</style>
</head>
<body>
<main class="sheet">
  <section class="card card-front" aria-label="Business card front">
    <svg class="panel-art" viewBox="0 0 540 320" aria-hidden="true">
      <path d="M257 0 C 318 95 300 235 200 320 L540 320 L540 0 Z" fill="var(--brand-green-light)"/>
      <path d="M247 0 C 308 95 290 235 190 320" fill="none" stroke="var(--brand-blue)" stroke-width="4"/>
    </svg>
    <div class="identity">
      <span class="brand-dot" aria-hidden="true"></span>
      <h1 class="holder-name">Morven Lisk</h1>
      <p class="strapline">Re-Vitalising High Achievers</p>
    </div>
    <ul class="contact-list">
      <li>
        <svg class="icon" viewBox="0 0 24 24" aria-hidden="true"><path d="M6.6 3.5l3 3.2-1.8 2.2c1 2.2 3 4.2 5.3 5.3l2.2-1.8 3.2 3-1.8 3.1C10.6 18.4 5.6 13.4 3.5 5.3z" fill="#fff"/></svg>
        <span>+44 7915 302618</span>
      </li>
      <li>
        <svg class="icon" viewBox="0 0 24 24" aria-hidden="true"><g fill="none" stroke="#fff" stroke-width="2"><circle cx="12" cy="12" r="9"/><ellipse cx="12" cy="12" rx="4" ry="9"/><path d="M3 12h18M5 7h14M5 17h14"/></g></svg>
        <span>www.morvenlisk.co.uk</span>
      </li>
      <li>
        <svg class="icon" viewBox="0 0 24 24" aria-hidden="true"><rect x="3" y="6" width="18" height="12" rx="1" fill="#fff"/><path d="M3 6l9 7 9-7" fill="none" stroke="var(--brand-green-light)" stroke-width="1.6"/></svg>
        <span>morven@morvenlisk.co.uk</span>
      </li>
      <li>
        <span class="icon-label">callnest</span>
        <span>morvenlisk</span>
      </li>
    </ul>
  </section>

  <section class="card card-back" aria-label="Business card back">
    <p class="back-name">Morven Lisk</p>
  </section>
</main>
</body>
</html>
```